Group training gym/bootcamp needs a web design

We need a website for our gym that is based in Sydney. We have indoor functional training classes and outdoor bootcamp classes. We would like the web site to have a video (to be created) and photo gallery. I would like the site made on word press and i would like to be able to make minor changes such as changing images and text without having to use a designer.

The website should have the following pages: home page; the gym; the bootcamp; photo gallery; about us; contact.

I have uploaded our logo and i would like to keep to these colour (blue,yellow,silver) and black is also allowed

Target Market(s)

18-50 male and female

Industry/Entity Type

Gym

Coding

Coded - Design and coding required

Number of Pages Required

5+ page

Font styles to use
Sans Serif

Colors
0692cd
fbed22
1b1b1b
e8e8e8

Requirements
Must have
• The website should have the following pages: home page; the gym; the bootcamp; photo gallery; about us; contact.
• I have uploaded our logo and i would like to keep to these colour (blue,yellow,silver) and black is also allowed
• Video upload and photo upload

```html
<!DOCTYPE html>
<html lang="en">
<head>
<meta charset="utf-8">
<title>Forge Fitness Hub</title>
<link rel="stylesheet" href="https://fonts.googleapis.com/css2?family=Oswald:wght@400;500;700&family=Roboto+Condensed:wght@400;700&display=swap">
<style>
:root{
  --blue:#0692cd;
  --yellow:#fbed22;
  --black:#1b1b1b;
  --silver:#e8e8e8;
  --ink:#2a2a2a;
  --text:#555;
  --white:#fff;
  --bar:#141414;
}
*{margin:0;padding:0;box-sizing:border-box}
html,body{width:1200px;height:2699px;overflow:hidden;background:var(--white)}
body{font-family:"Roboto Condensed",Arial,sans-serif;color:var(--text);position:relative}
.abs{position:absolute}
.head{font-family:"Oswald",Arial,sans-serif}

/* header */
.site-header{left:0;top:0;width:1200px;height:122px;background:var(--white);z-index:3}
.brand{left:99px;top:-18px;width:220px;height:220px;border-radius:50%;background:var(--white);z-index:4;display:flex;flex-direction:column;align-items:center;justify-content:center;padding-top:30px}
.brand-dot{width:54px;height:54px;border-radius:50%;background:var(--blue);margin-bottom:10px}
.brand-name{font-family:"Oswald",Arial,sans-serif;font-weight:700;font-size:21px;color:var(--blue);text-transform:uppercase;letter-spacing:.5px;text-align:center;line-height:1.05}
.nav{top:56px;left:0;width:1200px;height:24px;z-index:5}
.nav a{position:absolute;font-family:"Oswald",Arial,sans-serif;font-size:14.5px;color:#222;text-decoration:none;text-transform:uppercase;white-space:nowrap}
.nav a.active{color:var(--blue)}

/* hero */
.hero{left:0;top:122px;width:1200px;height:697px;background:linear-gradient(100deg,#4b4343 0%,#8a7e7a 30%,#b4aca6 55%,#d0cbc5 80%,#bfb8b0 100%)}
.hero-title{right:97px;top:318px;font-size:61px;font-weight:700;color:var(--white);letter-spacing:.5px;white-space:nowrap}
.hero-sub{right:97px;top:394px;font-family:"Oswald",Arial,sans-serif;font-weight:400;font-size:22px;color:var(--white);white-space:nowrap}
.arrow{width:50px;height:50px;top:348px}

/* class tiles */
.tile{top:723px;height:281px;display:flex;align-items:center;justify-content:center;text-align:center;font-family:"Oswald",Arial,sans-serif;font-weight:700;font-size:45px;line-height:1.12;color:var(--white);text-transform:uppercase}
.tile-indoor{left:99px;width:500px;background:linear-gradient(135deg,rgba(6,146,205,.95),rgba(80,170,215,.85))}
.tile-outdoor{left:603px;width:499px;background:linear-gradient(135deg,rgba(225,212,40,.95),rgba(236,222,30,.9))}

/* welcome */
.welcome-title{left:0;width:1200px;top:1072px;text-align:center;font-size:36px;font-weight:400;color:var(--ink);text-transform:uppercase}
.welcome-copy{left:194px;width:814px;top:1135px;text-align:center;font-size:13px;line-height:23px;color:#666}
.welcome-copy p+p{margin-top:22px}

/* video */
.video{left:0;top:1367px;width:1200px;height:419px;background:linear-gradient(90deg,#6b5140 0%,#8a6b55 30%,#a38b78 55%,#7b6a5f 80%,#5c4d44 100%)}
.video-title{left:0;width:1200px;top:1460px;text-align:center;font-size:50px;font-weight:700;color:var(--white);text-transform:uppercase}
.play{left:569px;top:1542px;width:60px;height:60px}

/* gallery */
.thumb{width:261px;height:187px;background:var(--white);border:1px solid #ddd;padding:7px}
.thumb div{width:100%;height:100%}
.gallery-title{left:676px;top:1880px;font-size:36px;font-weight:700;color:#2b2b2b;text-transform:uppercase}
.gallery-copy{left:682px;width:420px;top:1944px;font-size:13px;line-height:26px;color:#666}
.gallery-copy p+p{margin-top:14px}
.btn{left:682px;top:2224px;width:183px;height:45px;background:var(--blue);color:var(--white);font-family:"Oswald",Arial,sans-serif;font-weight:500;font-size:18px;display:flex;align-items:center;justify-content:center;text-transform:uppercase}

/* footer */
.footer{left:0;top:2367px;width:1200px;height:269px;background:var(--black)}
.col-title{font-family:"Oswald",Arial,sans-serif;font-weight:700;font-size:15px;color:var(--white);text-transform:uppercase;letter-spacing:.6px}
.col-list{list-style:none;font-size:12.5px;color:#bbb;line-height:27px}
.divider{top:2410px;width:1px;height:200px;background:#2c2c2c}
.news-copy{left:254px;top:2445px;width:260px;font-size:12.5px;line-height:20px;color:#bbb}
.news-input{left:254px;top:2492px;width:241px;height:41px;background:var(--white);font-size:10px;color:#999;padding:14px 12px}
.news-btn{left:254px;top:2547px;width:90px;height:42px;background:#000;color:var(--white);font-family:"Oswald",Arial,sans-serif;font-weight:700;font-size:13px;display:flex;align-items:center;justify-content:center;text-transform:uppercase}
.contact-name{font-weight:700;color:#ddd}
.contact-row{display:flex;align-items:center;gap:8px}
.bottom-bar{left:0;top:2636px;width:1200px;height:63px;background:var(--bar);font-size:12.5px;color:#aaa}
.social{width:12px;height:12px;border-radius:50%;background:#ddd;top:26px}
</style>
</head>
<body>

<header class="site-header abs"></header>
<div class="brand abs">
  <span class="brand-dot"></span>
  <span class="brand-name">Forge<br>Fitness Hub</span>
</div>
<nav class="nav abs">
  <a class="active" style="left:466px">Home</a>
  <a style="left:549px">The Gym</a>
  <a style="left:648px">The Bootcamp</a>
  <a style="left:785px">Photo Gallery</a>
  <a style="left:925px">About Us</a>
  <a style="left:1031px">Contact Us</a>
</nav>

<section class="hero abs" role="img" aria-label="Row of people doing push-ups on kettlebells in a gym"></section>
<h1 class="hero-title head abs">FORGE FITNESS HUB</h1>
<p class="hero-sub abs">We have indoor functional training classes and outdoor bootcamp classes</p>
<svg class="arrow abs" style="left:34px" viewBox="0 0 50 50"><circle cx="25" cy="25" r="23" fill="none" stroke="#fff" stroke-width="2"/><path d="M28 17l-8 8 8 8" fill="none" stroke="#fff" stroke-width="2"/></svg>
<svg class="arrow abs" style="left:1114px" viewBox="0 0 50 50"><circle cx="25" cy="25" r="23" fill="none" stroke="#fff" stroke-width="2"/><path d="M22 17l8 8-8 8" fill="none" stroke="#fff" stroke-width="2"/></svg>

<a class="tile tile-indoor abs" role="img" aria-label="Indoor training class with people on exercise machines">Indoor Functional<br>Training Classes</a>
<a class="tile tile-outdoor abs" role="img" aria-label="Outdoor bootcamp class stretching">Outdoor Bootcamp<br>Classes</a>

<h2 class="welcome-title head abs">Welcomet to Forge Fitness Hub</h2>
<div class="welcome-copy abs">
  <p>Lorem ipsum dolor sit amet, consectetur adipiscing elit, sed do eiusmod tempor incididunt ut labore et dolore magna aliqua. Ut enim ad minim veniam, quis nostrud exercitation ullamco laboris nisi ut aliquip ex ea commodo consequat. Duis aute irure dolor in reprehenderit in voluptate velit esse cillum dolore eu fugiat nulla pariatur.</p>
  <p>Sed ut perspiciatis unde omnis iste natus error sit voluptatem accusantium doloremque laudantium, totam rem aperiam, eaque ipsa quae ab illo inventore veritatis et quasi architecto beatae vitae dicta sunt explicabo. Nemo enim ipsam voluptatem quia voluptas sit aspernatur aut odit aut fugit, sed quia consequuntur magni dolores eos qui ratione voluptatem sequi nesciunt.</p>
</div>

<section class="video abs" role="img" aria-label="Woman doing a push-up on a gym floor"></section>
<h2 class="video-title head abs">Our Video</h2>
<svg class="play abs" viewBox="0 0 60 60"><circle cx="30" cy="30" r="27" fill="none" stroke="#fff" stroke-width="3"/><path d="M24 18l18 12-18 12z" fill="#fff"/></svg>

<div class="thumb abs" style="left:99px;top:1882px"><div role="img" aria-label="Trainer spotting a dumbbell bench press" style="background:linear-gradient(135deg,#1f2a2e,#4a5356)"></div></div>
<div class="thumb abs" style="left:381px;top:1882px"><div role="img" aria-label="Woman lifting a barbell with a trainer" style="background:linear-gradient(135deg,#d9d4cf,#8d7a70)"></div></div>
<div class="thumb abs" style="left:99px;top:2088px"><div role="img" aria-label="Woman doing a plank on dumbbells" style="background:linear-gradient(135deg,#e9e6e4,#c2514c)"></div></div>
<div class="thumb abs" style="left:381px;top:2088px"><div role="img" aria-label="Athlete gripping a barbell, black and white" style="background:linear-gradient(135deg,#2a2a2a,#8c8c8c)"></div></div>

<h2 class="gallery-title head abs">Photo Gallery</h2>
<div class="gallery-copy abs">
  <p>At vero eos et accusamus et iusto odio dignissimos ducimus qui blanditiis praesentium voluptatum deleniti atque corrupti quos dolores et quas molestias excepturi sint occaecati cupiditate non provident, similique sunt in culpa qui officia deserunt mollitia animi, id est laborum et dolorum fuga.</p>
  <p>But I must explain to you how all this mistaken idea of denouncing pleasure and praising pain was born and I will give you a complete account of the system, and expound the actual teachings of the great explorer of the truth, the master-builder of human happiness.</p>
</div>
<a class="btn abs">View More</a>

<footer class="footer abs"></footer>
<h4 class="col-title abs" style="left:99px;top:2405px">Links</h4>
<ul class="col-list abs" style="left:99px;top:2433px">
  <li>Home</li><li>The Gym</li><li>The Bootcamp</li><li>Photo Gallery</li><li>About us</li><li>Contact us</li>
</ul>
<span class="divider abs" style="left:207px"></span>
<h4 class="col-title abs" style="left:254px;top:2409px">Join Our Newsletter</h4>
<p class="news-copy abs">Excepteur sint occaecat cupidatat non proident, sunt in culpa qui</p>
<div class="news-input abs">Enter Your Email</div>
<div class="news-btn abs">Subscribe</div>
<span class="divider abs" style="left:548px"></span>
<h4 class="col-title abs" style="left:590px;top:2405px">Information</h4>
<ul class="col-list abs" style="left:590px;top:2433px">
  <li>Terms &amp; Conditions</li><li>Privacy policy</li><li>Disclaimer</li><li>Contact us</li><li>Sitemap</li>
</ul>
<span class="divider abs" style="left:736px"></span>
<h4 class="col-title abs" style="left:786px;top:2405px">Why Us</h4>
<ul class="col-list abs" style="left:786px;top:2433px">
  <li>Customers</li><li>Team</li><li>FAQ</li><li>News</li><li>Others</li>
</ul>
<span class="divider abs" style="left:906px"></span>
<h4 class="col-title abs" style="left:947px;top:2405px">Contact Info</h4>
<ul class="col-list abs" style="left:947px;top:2433px">
  <li class="contact-name">Forge Fitness Hub</li>
  <li style="line-height:20px;margin-top:4px">No Street Address,<br>State Code, Country</li>
  <li class="contact-row" style="margin-top:4px"><svg width="11" height="11" viewBox="0 0 24 24"><path fill="#ccc" d="M6.6 10.8a15 15 0 0 0 6.6 6.6l2.2-2.2c.3-.3.7-.4 1-.2 1.1.4 2.3.6 3.6.6.6 0 1 .4 1 1V20c0 .6-.4 1-1 1A17 17 0 0 1 3 4c0-.6.4-1 1-1h3.5c.6 0 1 .4 1 1 0 1.3.2 2.5.6 3.6.1.3 0 .7-.2 1z"/></svg>+61 (0) 200 481 73</li>
  <li class="contact-row"><svg width="11" height="9" viewBox="0 0 24 18"><rect width="24" height="18" fill="#ccc"/><path d="M0 0l12 9 12-9" fill="none" stroke="#1b1b1b" stroke-width="2"/></svg>hello@forgefitnesshub.com</li>
</ul>

<div class="bottom-bar abs">
  <span class="abs" style="left:99px;top:22px">© 2017. Forge Fitness Hub. All rights reserved</span>
  <span class="abs" style="left:777px;top:22px">Connect with our social network :</span>
  <span class="social abs" style="left:950px"></span>
  <span class="social abs" style="left:985px"></span>
  <span class="social abs" style="left:1020px"></span>
  <span class="social abs" style="left:1055px"></span>
  <span class="social abs" style="left:1090px"></span>
</div>

</body>
</html>
```